Rack Card for Charter Sail Boat business in SF Bay

We are in need of a rack card design to highlight the business to tourists and locals. 2 sided card 3.86" x 8.39" (full bleed)

We are looking for visually appleaing designs on the front and back but a little more detail on the back.

Use the info provided (text and info) on the website to include the 3 key services (Quick, 1/2 day, fullday) and aspects of the boat, location and other key info for customers (not prices). DO NOT INCLUDE ALL THIS TEXT please pick the elements you would like to fit your design and inform the customer as you would like about the business.

I can also provide photos directly from the video if you think those would fit your design. If video doesn't work on this upload you can view it at the website or facebook page (www.fb.com/tidewrenmarinellc)

Target Market(s)

Tourists and locals to san francisco east bay. 25 - 55 years old. Men and women.

Industry/Entity Type

Entertainment

Colors
0455a3
ec1f27
f3f1f8

Requirements
Must have
• Highlight services, key contact information (email, phone, website site), Visual impact
• 2-sided card - 3.86" x 8.39" (98 x 213 mm)
Nice to have
• facebook link, electric engine(green),

```html
<!DOCTYPE html>
<html lang="en">
<head>
<meta charset="utf-8">
<title>Tidewren Marine – Rack Card</title>
<link rel="stylesheet" href="https://fonts.googleapis.com/css2?family=Cinzel:wght@500&family=Oswald:wght@500&family=Raleway:wght@400;500&family=Roboto+Slab:wght@700;900&family=Tinos&display=swap">
<style>
  :root{
    --blue:#0455a3;
    --blue-deep:#0a4a97;
    --red:#ec1f27;
    --mist:#f3f1f8;
    --grey:#d6d7da;
    --ink:#1d1d1f;
    --white:#ffffff;
    --stage:#e6e6e8;
  }
  *{box-sizing:border-box;margin:0;padding:0}
  html,body{width:1200px;height:1000px;overflow:hidden;background:var(--stage)}
  .stage{position:relative;width:1200px;height:1000px}
  .card{position:absolute;top:38px;width:432px;height:922px;overflow:hidden;box-shadow:0 4px 14px rgba(0,0,0,.25)}
  .card--front{left:128px;background:linear-gradient(#e4e5e7,#c9cacd 20%,#d3d4d7 60%,#e8e8ea)}
  .card--back{left:620px;background:linear-gradient(180deg,#f6f6f8,#e3e6ec 50%,#f1f1f4)}
  .abs{position:absolute}

  /* brand mark */
  .brand{position:absolute;display:flex;align-items:center;gap:10px;font-family:"Roboto Slab",serif;font-weight:700}
  .brand__dot{border-radius:50%;flex:none}
  .brand--front{left:0;right:0;top:50px;justify-content:center;font-size:44px;color:var(--blue)}
  .brand--front .brand__dot{width:34px;height:34px;background:var(--blue)}
  .brand--back{left:22px;top:846px;font-size:26px;color:var(--white)}
  .brand--back .brand__dot{width:22px;height:22px;background:var(--white)}

  /* front */
  .banner{left:0;right:0;top:152px;height:32px;background:var(--red);color:var(--white);font-family:"Cinzel",serif;font-weight:500;font-size:17.5px;text-align:center;line-height:33px;letter-spacing:.2px}
  .hero{left:0;right:0;top:184px;height:356px;background:linear-gradient(180deg,#9fb9d6 0%,#b9c7d4 14%,#4f6f72 18%,#3f5a57 60%,#334b47 100%)}
  .hero-strip{left:0;right:0;top:537px;height:7px;background:var(--blue)}
  .feature{top:489px;width:121px;height:122px;border:3px solid var(--white);background:#6b7f8f}
  .feature__label{position:absolute;left:0;right:0;bottom:6px;text-align:center;color:var(--white);font-family:"Oswald",sans-serif;font-weight:500;font-size:17px;letter-spacing:.3px;text-shadow:0 1px 3px rgba(0,0,0,.8)}
  .feature--modern{left:25px;background:linear-gradient(#a9bccb,#5f7482 55%,#4a5c66)}
  .feature--entertaining{left:158px;background:linear-gradient(#7fa9cf,#3f5e78 50%,#2c3f4d)}
  .feature--safe{left:287px;background:linear-gradient(#3c4b5e,#8a7c72 55%,#d89a52 70%,#2d3440)}
  .feature-text{top:618px;width:122px;font-family:"Tinos",serif;font-size:10.2px;line-height:12.7px;color:var(--ink);text-align:center}
  .feature-text--a{left:24px}.feature-text--b{left:157px}.feature-text--c{left:290px;text-align:left}

  /* contact footer */
  .footer{left:0;right:0;top:790px;height:132px}
  .footer svg{position:absolute;left:0;top:0}
  .contact{position:absolute;color:var(--white);font-family:"Raleway",sans-serif}
  .contact__intro{font-size:12.2px}
  .contact__phone{font-family:"Roboto Slab",serif;font-weight:700;font-size:20px;display:flex;align-items:center;gap:8px;letter-spacing:.3px}
  .contact__phone svg{position:static}
  .contact__line{font-size:13px;font-weight:500;letter-spacing:.2px}
  .socials{display:flex;gap:7px}
  .socials span{width:15px;height:15px;border-radius:2px;background:#6f9fd6}
  .contact--front{left:0;right:0;top:15px;text-align:center}
  .contact--front .contact__phone{justify-content:center;margin:6px 0 4px}
  .contact--front .contact__line{line-height:19px}
  .contact--front .socials{justify-content:center;margin-top:9px}
  .contact--back{left:173px;top:22px;width:240px}
  .contact--back .contact__intro{font-size:10.5px}
  .contact--back .contact__phone{font-size:15px;margin:6px 0 6px;gap:6px}
  .contact--back .contact__line{font-size:11.5px;line-height:19px}
  .contact--back .socials{position:absolute;right:10px;top:58px}

  /* back */
  .intro{left:0;right:0;top:0;height:194px;background:var(--blue)}
  .intro__title{position:absolute;left:0;right:0;top:26px;text-align:center;color:var(--white);font-family:"Roboto Slab",serif;font-weight:900;font-size:24px;letter-spacing:.5px}
  .intro__text{position:absolute;left:22px;right:20px;top:62px;color:#eaf0f8;font-family:"Raleway",sans-serif;font-size:13.4px;line-height:18px}
  .intro-rule{left:0;right:0;top:194px;height:4px;background:var(--red)}
  .sail-wash{left:0;right:0;top:198px;height:600px;background:radial-gradient(ellipse at 70% 30%,rgba(255,255,255,.8),rgba(214,220,230,.5) 60%,rgba(240,240,244,.2))}
  .trip-tag{left:125px;top:183px;width:174px;height:42px;background:var(--red);border-radius:5px;color:var(--white);font-family:"Roboto Slab",serif;font-weight:900;font-size:26px;text-align:center;line-height:42px;box-shadow:0 1px 3px rgba(0,0,0,.3)}
  .route{width:124px;height:124px;border-radius:50%;border:4px solid var(--white);box-shadow:0 0 0 2px var(--blue);background:radial-gradient(circle at 40% 45%,#cfe6c6,#dce9ee 40%,#b9d5ea 75%,#e9eef1)}
  .route--blast{left:22px;top:238px}
  .route--half{left:281px;top:370px}
  .route--full{left:22px;top:514px}
  .route--custom{left:281px;top:640px;background:radial-gradient(circle at 55% 62%,#fff3b0,#f7a83a 18%,#b86b2f 45%,#6f4f46 70%,#4e5a76)}
  .trip{position:absolute;width:250px}
  .trip__name{font-family:"Roboto Slab",serif;font-weight:700;font-size:18.5px;color:var(--blue);letter-spacing:.3px}
  .trip__text{font-family:"Tinos",serif;font-size:13px;line-height:16.4px;color:var(--ink);margin-top:1px}
  .trip--blast{left:163px;top:256px}
  .trip--half{left:22px;top:382px;text-align:right;width:246px}
  .trip--full{left:163px;top:524px}
  .trip--custom{left:20px;top:640px;text-align:right;width:248px}
</style>
</head>
<body>
<main class="stage">

  <!-- Front side -->
  <section class="card card--front" aria-label="Rack card front">
    <div class="brand brand--front"><span class="brand__dot"></span>Tidewren</div>
    <div class="abs banner">ULTIMATE EAST BAY SAILBOAT CHARTER</div>
    <div class="abs hero" role="img" aria-label="Photo of the sailboat under full sail on the bay with hills behind"></div>
    <div class="abs hero-strip"></div>

    <div class="abs feature feature--modern" role="img" aria-label="Photo of the deck looking forward over the water"><span class="feature__label">MODERN</span></div>
    <div class="abs feature feature--entertaining" role="img" aria-label="Photo of guests in life jackets at the helm"><span class="feature__label">ENTERTAINING</span></div>
    <div class="abs feature feature--safe" role="img" aria-label="Photo of the rail at sunset"><span class="feature__label">SAFE</span></div>

    <p class="abs feature-text feature-text--a">Tidewren has gone completely electric which means no diesel smells, noise or vibration to suffer. New electrics, plumbing, toilets, and deck areas compliment the elegant lines and features of this Harlan Whitby 46 foot cutter rigged sailboat.</p>
    <p class="abs feature-text feature-text--b">Surrounded by the beauty and wonder of the San Francisco Bay you will enjoy the choice of sounds from your source, CD or old school FM! You can take the helm to experience the thrill of sailing Tidewren while we explore Alcatraz and Angel Islands.</p>
    <p class="abs feature-text feature-text--c">The safety of everyone aboard is paramount to our business and your enjoyment. We carry aboard everything to make your time aboard safe. Life preservers are provided and available for all including kids sizes. We carry self inflating slim comfortable life jackets.</p>

    <div class="abs footer">
      <svg width="432" height="132" viewBox="0 0 432 132" aria-hidden="true">
        <path d="M0 16 Q216 -6 432 16 V132 H0 Z" fill="var(--blue-deep)"/>
        <path d="M0 12 Q216 -10 432 12" fill="none" stroke="#ffffff" stroke-width="3"/>
      </svg>
      <div class="contact contact--front">
        <p class="contact__intro">For more detailed information call or click</p>
        <p class="contact__phone">
          <svg width="20" height="20" viewBox="0 0 20 20" aria-hidden="true"><circle cx="10" cy="10" r="8.5" fill="none" stroke="#fff" stroke-width="1.6"/><path d="M7 5.5c.6-.3 1.1 0 1.3.5l.6 1.4c.2.4 0 .8-.3 1l-.6.5c.4 1 1.2 1.8 2.2 2.2l.5-.6c.3-.3.7-.4 1-.3l1.4.6c.5.2.7.8.5 1.3-.4 1-1.4 1.5-2.4 1.2-2.4-.8-4.3-2.7-5-5.1-.3-1 .2-2.1.8-2.7z" fill="#fff"/></svg>
          +1 (510) 555 SAIL (7245)
        </p>
        <p class="contact__line">bookings@TidewrenMarine.com</p>
        <p class="contact__line">www.tidewrenmarine.com</p>
        <div class="socials"><span></span><span></span><span></span></div>
      </div>
    </div>
  </section>

  <!-- Back side -->
  <section class="card card--back" aria-label="Rack card back">
    <div class="abs sail-wash" role="img" aria-label="Faint photo of sails and rigging in the background"></div>
    <div class="abs intro">
      <h1 class="intro__title">WHAT IS TIDEWREN?</h1>
      <p class="intro__text">Tidewren is a 50 foot, center cockpit, cutter rigged, mono-hulled, blue water cruising sail boat. She's a nice sized boat with the driving position and main seats at the center of the boat. She has three positions for sails, main (the big one), jib (front sail) and stay-sail (between main and jib). She has a single hull so will lean over as the wind blows.</p>
    </div>
    <div class="abs intro-rule"></div>
    <div class="abs trip-tag">THE TRIP</div>

    <div class="abs route route--blast" role="img" aria-label="Map of the short bay route"></div>
    <div class="trip trip--blast">
      <h2 class="trip__name">2 HOUR BLAST</h2>
      <p class="trip__text">Could be a sunset sail, an early morning wake up cruise or a blast out into the bay anytime to find peace, fresh air and amazing views.</p>
    </div>

    <div class="abs route route--half" role="img" aria-label="Map of the half day bay route"></div>
    <div class="trip trip--half">
      <h2 class="trip__name">1/2 DAY FUN</h2>
      <p class="trip__text">Could be a sunset sail, an early morning wake up cruise or a blast out into the bay anytime to find peace, fresh air and amazing views.</p>
    </div>

    <div class="abs route route--full" role="img" aria-label="Map of the full circuit of the bay"></div>
    <div class="trip trip--full">
      <h2 class="trip__name">FULL DAY ADVENTURE</h2>
      <p class="trip__text">The day includes a complete circuit of the Bay and lunch at anchor. Actual duration 7-8 hours</p>
    </div>

    <div class="abs route route--custom" role="img" aria-label="Photo of the bay bridge at sunset"></div>
    <div class="trip trip--custom">
      <h2 class="trip__name">CUSTOM CRUISE</h2>
      <p class="trip__text">You decide and we'll make it happen. When booking online just select the day and start time as normal and then ,record the length of trip you are looking for as text in the comments and we will get into contact with you to sort it out.</p>
    </div>

    <div class="abs footer">
      <svg width="432" height="132" viewBox="0 0 432 132" aria-hidden="true">
        <path d="M0 16 Q216 -6 432 16 V132 H0 Z" fill="var(--blue-deep)"/>
        <path d="M0 12 Q216 -10 432 12" fill="none" stroke="#ffffff" stroke-width="3"/>
      </svg>
      <div class="contact contact--back">
        <p class="contact__intro">For more detailed information call or click</p>
        <p class="contact__phone">
          <svg width="15" height="15" viewBox="0 0 20 20" aria-hidden="true"><circle cx="10" cy="10" r="8.5" fill="none" stroke="#fff" stroke-width="1.8"/><path d="M7 5.5c.6-.3 1.1 0 1.3.5l.6 1.4c.2.4 0 .8-.3 1l-.6.5c.4 1 1.2 1.8 2.2 2.2l.5-.6c.3-.3.7-.4 1-.3l1.4.6c.5.2.7.8.5 1.3-.4 1-1.4 1.5-2.4 1.2-2.4-.8-4.3-2.7-5-5.1-.3-1 .2-2.1.8-2.7z" fill="#fff"/></svg>
          +1 (510) 555 SAIL (7245)
        </p>
        <p class="contact__line">bookings@TidewrenMarine.com</p>
        <p class="contact__line">www.tidewrenmarine.com</p>
        <div class="socials"><span></span><span></span><span></span></div>
      </div>
    </div>
    <div class="brand brand--back"><span class="brand__dot"></span>Tidewren</div>
  </section>

</main>
</body>
</html>
```